Help our Sugar Loom find our winning design! We're looking for a business card....

We’re a Sugar Loom in NY specializing in custom-made cakes and unique desserts.
Our cakes combine flavor and art, each designed to match customer’s special event and theme.
We’d like a unique business card with a clean design that will combine French chic and artistic look & feel.
We’d like to differentiate ourselves from standard bakeries, please don’t offer cupcake images :-)
Our logo is peach-pink and brown and we’d love to use these colors ( . Another color that can be added is gold - or feel free to suggest!

Target Market(s)

Women, ages 25-55

Industry/Entity Type

Boutique

Contact Information for Business Card

Text on card:
Logo
Sugar Loom by Dana Welch

www.sugarloomsweets.com
hello@sugarloom.com
(516) 555-0147
F – sugarloomnyc
IG - sugarloom_ny

Font styles to use
Sans Serif
Script

Requirements
Must have
• Logo
• Clean look
• French chic and artistic look & feel.
Nice to have
• Damask pattern
Should not have
• Cupcake images

```html
<!DOCTYPE html>
<html lang="en">
<head>
<meta charset="utf-8">
<title>Sugar Loom – Business Card</title>
<link rel="stylesheet" href="https://fonts.googleapis.com/css2?family=Lato:wght@400;700&family=Great+Vibes&display=swap">
<style>
  :root {
    --backdrop: #dcdcdc;
    --cocoa: #231617;
    --cocoa-soft: #3a2526;
    --gold: #c9a04a;
    --gold-deep: #9a7428;
    --gold-light: #f0cf74;
    --blush: #e2b2ad;
    --blush-soft: #f3dcd8;
    --paper: #ffffff;
    --ink: #3b2a28;
    --icon-gold: #c8a043;
  }
  * { box-sizing: border-box; margin: 0; padding: 0; }
  html, body { width: 1200px; height: 852px; overflow: hidden; }
  body {
    background: var(--backdrop);
    font-family: "Lato", sans-serif;
    display: flex;
    align-items: center;
    justify-content: center;
    gap: 60px;
  }
  .card {
    position: relative;
    width: 520px;
    height: 297px;
    border-radius: 18px;
    overflow: hidden;
  }
  /* Back side */
  .card--back {
    background: radial-gradient(ellipse at 45% 40%, var(--cocoa-soft), var(--cocoa) 70%);
    display: flex;
    align-items: center;
    justify-content: center;
    gap: 14px;
  }
  .brand-dot {
    width: 14px; height: 14px; border-radius: 50%;
    background: var(--gold);
  }
  .brand-name {
    font-family: "Lato", sans-serif;
    font-weight: 400;
    letter-spacing: 2px;
  }
  .card--back .brand-name { color: var(--gold); font-size: 38px; }
  /* Front side */
  .card--front { background: linear-gradient(160deg, var(--paper) 40%, #f6efee); }
  .swoosh { position: absolute; inset: 0; width: 100%; height: 100%; }
  .brand-lockup {
    position: absolute; left: 42px; top: 70px;
    display: flex; align-items: center; gap: 10px;
  }
  .brand-lockup .brand-dot { background: var(--blush); width: 11px; height: 11px; }
  .card--front .brand-name { color: var(--ink); font-size: 28px; }
  .contact-list {
    position: absolute; left: 42px; top: 172px;
    list-style: none;
    font-size: 12.5px; color: var(--ink);
  }
  .contact-list li { display: flex; align-items: center; gap: 9px; height: 18px; }
  .contact-icon { width: 11px; height: 11px; flex: none; }
  .social-squares { display: flex; gap: 2px; }
  .social-squares span { width: 9px; height: 9px; background: var(--icon-gold); border-radius: 1px; }
  .owner {
    position: absolute; right: 28px; top: 184px;
    text-align: center; color: var(--paper);
  }
  .owner-studio { font-size: 13px; letter-spacing: .3px; }
  .owner-name { font-family: "Great Vibes", cursive; font-size: 30px; line-height: 1.1; }
</style>
</head>
<body>
  <section class="card card--back" aria-label="Card back">
    <span class="brand-dot"></span>
    <span class="brand-name">Sugar Loom</span>
  </section>

  <section class="card card--front" aria-label="Card front">
    <svg class="swoosh" viewBox="0 0 520 297" preserveAspectRatio="none" aria-hidden="true">
      <defs>
        <linearGradient id="gold-sweep" x1="0" y1="1" x2="1" y2="0">
          <stop offset="0" stop-color="#f0cf74"/>
          <stop offset="0.45" stop-color="#c9a04a"/>
          <stop offset="1" stop-color="#8d6a24"/>
        </linearGradient>
      </defs>
      <path d="M520,38 C410,78 360,205 112,297 L150,297 C372,208 416,92 520,52 Z" fill="var(--blush)"/>
      <path d="M520,58 C422,95 385,205 172,297 L520,297 Z" fill="url(#gold-sweep)"/>
      <path d="M18,297 C150,286 255,262 335,222 L342,230 C272,272 170,294 64,297 Z" fill="var(--blush)"/>
      <path d="M0,276 C130,276 240,256 320,224 L324,229 C246,264 140,284 0,286 Z" fill="var(--blush-soft)"/>
    </svg>

    <div class="brand-lockup">
      <span class="brand-dot"></span>
      <span class="brand-name">Sugar Loom</span>
    </div>

    <ul class="contact-list">
      <li>
        <svg class="contact-icon" viewBox="0 0 12 12"><rect width="12" height="12" rx="1.5" fill="var(--icon-gold)"/><path d="M3.5 3h1.6l.6 1.6-1 .7a5 5 0 0 0 2 2l.7-1 1.6.6V8.5A1 1 0 0 1 8 9.4 6 6 0 0 1 2.6 4 1 1 0 0 1 3.5 3z" fill="#fff"/></svg>
        (516) 555-0147
      </li>
      <li>
        <svg class="contact-icon" viewBox="0 0 12 12"><rect width="12" height="12" rx="1.5" fill="var(--icon-gold)"/><rect x="2.5" y="3.5" width="7" height="5" fill="none" stroke="#fff"/><path d="M2.5 3.5 6 6.3 9.5 3.5" fill="none" stroke="#fff"/></svg>
        hello@sugarloom.com
      </li>
      <li>
        <svg class="contact-icon" viewBox="0 0 12 12"><circle cx="6" cy="6" r="6" fill="var(--icon-gold)"/><circle cx="6" cy="6" r="3.4" fill="none" stroke="#fff" stroke-width=".9"/><path d="M2.6 6h6.8M6 2.6c-1.6 2-1.6 4.8 0 6.8M6 2.6c1.6 2 1.6 4.8 0 6.8" fill="none" stroke="#fff" stroke-width=".7"/></svg>
        www.sugarloomsweets.com
      </li>
      <li>
        <span class="social-squares"><span></span><span></span></span>
        \sugarloomnyc
      </li>
    </ul>

    <div class="owner">
      <p class="owner-studio">Sugar Loom by</p>
      <p class="owner-name">Dana Welch</p>
    </div>
  </section>
</body>
</html>
```